Brightmill Data Works

Our company is about IT hardwares and IT solutions. IT hardware such as PC, RAMS, storage and servers. IT solutions such as project management, BA. We are also selling new technology too.

Target Market(s)

Consumer, Small to Medium Business, Corporate

Requirements
Must have
• The business card must have the following:
• Name:
• Title:
• Contact Number:
• Email address:
• Website:
• Color: Must match the logo color upgrade

```html
<!DOCTYPE html>
<html lang="en">
<head>
<meta charset="utf-8">
<title>Brightmill Data Works — Business Card</title>
<link rel="stylesheet" href="https://fonts.googleapis.com/css2?family=Saira+Semi+Condensed:wght@700&family=Roboto:wght@400;500&display=swap">
<style>
  :root {
    --backdrop: #e8e6e4;
    --paper: #fbfbfa;
    --ink: #3a3a3c;
    --orange-light: #dd8f2c;
    --orange-deep: #b9602a;
    --on-orange: #ffffff;
  }
  * { margin: 0; padding: 0; box-sizing: border-box; }
  html, body {
    width: 1200px; height: 997px; overflow: hidden;
    background: var(--backdrop);
  }
  .stage { position: relative; width: 1200px; height: 997px; }
  .card {
    position: absolute; width: 500px; height: 286px;
    background: var(--paper);
    box-shadow: 0 10px 26px rgba(0,0,0,.12), 0 2px 4px rgba(0,0,0,.08);
    overflow: hidden;
  }
  .card--front { left: 110px; top: 170px; }
  .card--back  { left: 590px; top: 500px; }

  .wordmark {
    font-family: "Saira Semi Condensed", sans-serif;
    font-weight: 700; color: var(--ink);
    text-transform: uppercase; line-height: 1.05;
  }
  .front-lockup {
    position: absolute; inset: 0;
    display: flex; flex-direction: column; align-items: center; justify-content: center;
    gap: 14px;
  }
  .front-lockup .mark-square {
    width: 26px; height: 26px; background: var(--orange-light); border-radius: 3px;
  }
  .front-lockup .wordmark { font-size: 34px; text-align: center; letter-spacing: .5px; }

  .back-band { position: absolute; inset: 0; width: 500px; height: 286px; }
  .back-wordmark {
    position: absolute; left: 300px; top: 112px; width: 180px;
    font-size: 22px; text-align: center;
  }
  .holder {
    position: absolute; left: 38px; top: 88px; color: var(--on-orange);
  }
  .holder__name {
    font-family: "Saira Semi Condensed", sans-serif; font-weight: 700;
    font-size: 19px; text-transform: uppercase; letter-spacing: .3px;
  }
  .holder__title {
    font-family: "Roboto", sans-serif; font-size: 10.5px; text-transform: uppercase;
    margin-top: 1px;
  }
  .contact {
    position: absolute; left: 52px; bottom: 38px; list-style: none;
    font-family: "Roboto", sans-serif; font-size: 11px; line-height: 1.45;
    color: var(--on-orange);
  }
</style>
</head>
<body>
<main class="stage">
  <section class="card card--front" aria-label="Card front">
    <div class="front-lockup">
      <span class="mark-square"></span>
      <div class="wordmark">Brightmill<br>Data Works</div>
    </div>
  </section>

  <section class="card card--back" aria-label="Card back">
    <svg class="back-band" viewBox="0 0 500 286" aria-hidden="true">
      <defs>
        <linearGradient id="orangeFill" x1="0" y1="1" x2="1" y2="0">
          <stop offset="0" stop-color="var(--orange-deep)"/>
          <stop offset="1" stop-color="var(--orange-light)"/>
        </linearGradient>
      </defs>
      <path fill="url(#orangeFill)" d="M0 0 H290 L220 286 H0 Z"/>
    </svg>
    <div class="wordmark back-wordmark">Brightmill<br>Data Works</div>
    <div class="holder">
      <p class="holder__name">Dana Whitlow</p>
      <p class="holder__title">CEO/Founder</p>
    </div>
    <ul class="contact">
      <li>555 204 7718</li>
      <li>dana@brightmilldata.com</li>
      <li>www.brightmilldata.com</li>
    </ul>
  </section>
</main>
</body>
</html>
```